Business card design for Quellan Engineering Tandem

We need a new business card design along with all the necessary to place an order. The company is Quellan Engineering Tandem and we recently updated our logo.

```html
<!DOCTYPE html>
<html lang="en">
<head>
<meta charset="utf-8">
<title>Quellan Engineering Tandem – Business Card</title>
<link rel="stylesheet" href="https://fonts.googleapis.com/css2?family=Jost:wght@400;500;700&display=swap">
<style>
  :root {
    --stage: #2b2b2b;
    --card: #1e1e1e;
    --emboss: #555555;
    --gray: #9a9a9a;
    --light: #c9c9c9;
    --yellow: #f2c21b;
    --band-gray: #8a8a8a;
    --rule: #6d6d6d;
  }
  * { margin: 0; padding: 0; box-sizing: border-box; }
  html, body { width: 1200px; height: 982px; overflow: hidden; }
  body {
    background: var(--stage);
    font-family: "Jost", sans-serif;
    position: relative;
  }
  .card {
    position: absolute;
    left: 320px;
    width: 560px;
    height: 320px;
    background: var(--card);
    border-radius: 18px;
    overflow: hidden;
    box-shadow: 0 10px 30px rgba(0,0,0,.45);
  }
  .card--front { top: 100px; }
  .card--back { top: 520px; }

  .brand {
    font-weight: 700;
    text-transform: uppercase;
    letter-spacing: 1px;
    line-height: 1;
    white-space: nowrap;
  }
  .card--front .brand {
    position: absolute;
    left: 0; right: 0; top: 50%;
    transform: translateY(-50%);
    text-align: center;
    font-size: 26px;
    color: var(--emboss);
  }
  .card--back .brand {
    position: absolute;
    right: 30px; top: 66px;
    font-size: 16px;
    color: var(--gray);
  }

  .person { position: absolute; left: 34px; top: 40px; }
  .person__name { color: var(--gray); font-weight: 700; font-size: 26px; letter-spacing: .5px; text-transform: uppercase; line-height: 1.05; }
  .person__role { color: var(--yellow); font-size: 15px; margin-top: 2px; }

  .rule { position: absolute; height: 1px; background: var(--rule); }
  .rule--main { left: 34px; right: 30px; top: 116px; }
  .rule--address { left: 320px; right: 30px; top: 206px; }

  .contacts { position: absolute; left: 34px; top: 130px; list-style: none; }
  .contacts li { display: flex; align-items: center; gap: 10px; color: var(--light); font-size: 14px; height: 22px; }
  .contacts svg { width: 13px; height: 13px; fill: var(--yellow); flex: none; }

  .address { position: absolute; right: 30px; top: 214px; text-align: right; font-size: 13px; line-height: 1.4; color: var(--light); font-style: normal; }
  .address__company { color: var(--yellow); font-size: 14px; }

  .band { position: absolute; bottom: 0; height: 10px; }
  .band--gray { left: 0; width: 62%; background: var(--band-gray); }
  .band--yellow { right: 0; width: 38%; background: var(--yellow); }
</style>
</head>
<body>

<section class="card card--front">
  <div class="brand">Quellan Engineering Tandem</div>
</section>

<section class="card card--back">
  <div class="person">
    <p class="person__name">Marcus Holt</p>
    <p class="person__role">Founder &amp; CEO</p>
  </div>

  <div class="brand">Quellan Engineering Tandem</div>

  <div class="rule rule--main"></div>

  <ul class="contacts">
    <li><svg viewBox="0 0 24 24"><path d="M6.6 10.8a15 15 0 0 0 6.6 6.6l2.2-2.2a1 1 0 0 1 1-.25 11.4 11.4 0 0 0 3.6.57 1 1 0 0 1 1 1V20a1 1 0 0 1-1 1A17 17 0 0 1 3 4a1 1 0 0 1 1-1h3.5a1 1 0 0 1 1 1c0 1.25.2 2.45.57 3.57a1 1 0 0 1-.25 1z"/></svg>(123) 456-7890</li>
    <li><svg viewBox="0 0 24 24"><path d="M7 1h10a2 2 0 0 1 2 2v18a2 2 0 0 1-2 2H7a2 2 0 0 1-2-2V3a2 2 0 0 1 2-2zm0 3v14h10V4zm5 15.5a1 1 0 1 0 0 2 1 1 0 0 0 0-2z"/></svg>(123) 456-7890</li>
    <li><svg viewBox="0 0 24 24"><path d="M6 2h12v5H6zM4 8h16a2 2 0 0 1 2 2v7h-4v5H6v-5H2v-7a2 2 0 0 1 2-2zm4 8v4h8v-4z"/></svg>(123) 456-7890</li>
    <li><svg viewBox="0 0 24 24"><path d="M2 5h20v14H2zm2 2v.5l8 5 8-5V7l-8 5z"/></svg>info@yourwebsitehere.com</li>
  </ul>

  <div class="rule rule--address"></div>

  <address class="address">
    <p class="address__company">Quellan Engineering Tandem</p>
    <p>423 Street Address Here, City</p>
    <p>State, Country, ZIP Code</p>
    <p>www.yourwebsitehere.com</p>
  </address>

  <div class="band band--gray"></div>
  <div class="band band--yellow"></div>
</section>

</body>
</html>
```